Pixorama Pages with Bold Font

I want the font to be simple yet bold for Pixorama images. Its all about a simple bold readable font. I need a single pixorama page with an image and copy/text on or over the image. The words will change in the future. I'm looking for the right font. I like fiery red and yellow colors. The "One Pic" attached is a sample of what I want without the Veltro words.

```html
<!DOCTYPE html>
<html lang="en">
<head>
<meta charset="utf-8">
<title>Pixorama Page – Shrink Your Gut</title>
<link rel="stylesheet" href="https://fonts.googleapis.com/css2?family=Teko:wght@600&family=Open+Sans:ital,wght@1,600;1,700&display=swap">
<style>
  :root {
    --fiery-red: #ff0000;
    --bright-yellow: #ffcc00;
    --shadow-dark: #141211;
    --photo-warm: #6b4a36;
    --photo-skin: #a9744f;
    --photo-sheet: #d9d6d2;
  }
  html, body {
    margin: 0;
    padding: 0;
    width: 1200px;
    height: 1200px;
    overflow: hidden;
    background: var(--shadow-dark);
  }
  .page {
    position: relative;
    width: 1200px;
    height: 1200px;
    overflow: hidden;
  }
  .hero-photo {
    position: absolute;
    inset: 0;
    background:
      radial-gradient(ellipse 30% 45% at 66% 52%, var(--photo-skin) 0%, rgba(169,116,79,0.55) 45%, rgba(0,0,0,0) 75%),
      radial-gradient(ellipse 45% 30% at 55% 92%, var(--photo-sheet) 0%, rgba(217,214,210,0.35) 50%, rgba(0,0,0,0) 80%),
      radial-gradient(ellipse 55% 55% at 60% 60%, var(--photo-warm) 0%, rgba(0,0,0,0) 75%),
      linear-gradient(180deg, #1c1a19 0%, #2a2420 55%, #3a3532 100%);
  }
  .copy {
    position: absolute;
    left: 76px;
    top: 0;
  }
  .headline {
    position: absolute;
    left: 0;
    margin: 0;
    font-family: "Teko", "Arial Narrow", sans-serif;
    font-weight: 600;
    color: var(--fiery-red);
    text-transform: uppercase;
    line-height: 1;
    white-space: nowrap;
    letter-spacing: -0.5px;
  }
  .headline--top {
    top: 236px;
    font-size: 96px;
    transform: scaleY(1.08);
    transform-origin: top left;
  }
  .headline--bottom {
    top: 822px;
    font-size: 92px;
    transform: scaleY(1.08);
    transform-origin: top left;
  }
  .line {
    position: absolute;
    left: 0;
    margin: 0;
    font-family: "Open Sans", "Calibri", sans-serif;
    font-style: italic;
    color: var(--bright-yellow);
    white-space: nowrap;
    text-align: justify;
    text-align-last: justify;
  }
  .subhead {
    width: 504px;
    font-size: 27px;
    font-weight: 700;
    text-transform: uppercase;
  }
  .subhead--1 { top: 310px; }
  .subhead--2 { top: 350px; }
  .story {
    width: 457px;
    font-size: 21px;
    font-weight: 600;
  }
  .story--1 { top: 453px; }
  .story--2 { top: 486px; }
  .story--3 { top: 520px; }
  .story--4 { top: 553px; }
  .question {
    width: 457px;
    font-size: 33px;
    font-weight: 600;
  }
  .question--1 { top: 612px; }
  .question--2 { top: 660px; }
  .invite {
    top: 780px;
    font-size: 26px;
    font-weight: 600;
    text-align: left;
    text-align-last: left;
  }
</style>
</head>
<body>
  <main class="page">
    <div class="hero-photo" role="img" aria-label="Moody warm-toned photo of a fit woman in nude lingerie seated on a bed with white sheets in a dark bedroom"></div>

    <section class="copy">
      <h1 class="headline headline--top">Helping more guys</h1>

      <p class="line subhead subhead--1">Get hot, sweaty &amp; hard than a</p>
      <p class="line subhead subhead--2">Vegas hooker on a Friday night.</p>

      <p class="line story story--1">As a fitness trainer for men I figured</p>
      <p class="line story story--2">if you wanted Tits &amp; Ass I'd give</p>
      <p class="line story story--3">it to you. At least long enough to make a</p>
      <p class="line story story--4">buck and get my guys in shape.</p>

      <p class="line question question--1">You wanna lose weight?</p>
      <p class="line question question--2">You wanna shrink that gut?</p>

      <p class="line invite">Touch me down here.</p>

      <h2 class="headline headline--bottom">I can help you shrink your gut.</h2>
    </section>
  </main>
</body>
</html>
```